Design a 8 site brochure A4 - we use a template for some things and the rest is to design from sr...

Pls design a brochure for us.We will use this template (we will provide the template to you): https://graphicriver.net/item/brochure/19300045?s_rank=2So in Total there will be 8 pages. The 1st and 8th page are fixed. This will be Title and End Page like in the template. We will provide pictures and so on for you in the end. For the rest of the page 2-7 you need to design it from sratch or you can use some parts of the template. We need the following information in there:• Text what our Idea is about• How it works there are 4 steps• The advantages for the business• The advantages for the customers oft he business• The Order Types & for who our App is made• The vision & Mission• Team Page (there will be 2 people)• There can also be some pictures of the app some phone mockups whatever looks good.. we leave it up to you• FAQ for the businessYou are more or less free to design it like you want and how much space or pages each section uses. Just hold the sequence like on top. It should be readable in A4 for each page and thats it rest is up to you.You can find images and the text in this Trello:https://trello.com/invite/b/0IepHaTk/33ce2769ddf69b3de7e1c8afa05f994e/flyer-businessPls make an account so then you can find the template logo and information in thereThanks a lot 😊
App

```html
<!DOCTYPE html>
<html lang="de">
<head>
<meta charset="utf-8">
<title>MesaOrder – Vorteile für Kunden</title>
<link href="https://fonts.googleapis.com/css2?family=Open+Sans:wght@300;400;600&display=swap" rel="stylesheet">
<style>
  :root {
    --red: #e3262b;
    --red-glass: rgba(200, 30, 35, 0.55);
    --charcoal: #353a3f;
    --ink: #222426;
    --body: #555a5e;
    --paper: #ffffff;
    --photo-dark: #3b2e28;
    --photo-light: #8a7c70;
  }
  * { margin: 0; padding: 0; box-sizing: border-box; }
  html, body { width: 851px; height: 1200px; overflow: hidden; background: var(--paper); }
  body { font-family: "Open Sans", Arial, sans-serif; }
  .page { position: relative; width: 851px; height: 1200px; overflow: hidden; background: var(--paper); }
  .hero-art { position: absolute; inset: 0; width: 851px; height: 760px; }
  .headline {
    position: absolute; top: 600px; left: 0; width: 851px;
    text-align: center; font-weight: 300; font-size: 37px; line-height: 1.3;
    color: var(--ink);
  }
  .benefits {
    position: absolute; top: 706px; left: 60px; width: 731px;
    display: flex; justify-content: space-between;
  }
  .benefit { width: 220px; text-align: center; }
  .benefit-icon { width: 92px; height: 100px; display: block; margin: 0 auto 14px; }
  .benefit-title {
    font-weight: 400; font-size: 20px; line-height: 1.2; color: var(--red);
    min-height: 50px; margin-bottom: 12px;
  }
  .benefit-title.is-dark { color: var(--ink); }
  .benefit-text { font-size: 11.5px; line-height: 1.45; color: var(--body); padding: 0 8px; }
  .footer {
    position: absolute; left: 42px; top: 1120px;
    display: flex; align-items: center; gap: 14px;
    font-size: 12px; color: var(--body);
  }
  .page-number {
    width: 22px; height: 22px; background: var(--red); color: var(--paper);
    font-size: 12px; display: flex; align-items: center; justify-content: center;
  }
</style>
</head>
<body>
<main class="page">
  <svg class="hero-art" viewBox="0 0 851 760">
    <defs>
      <linearGradient id="cafeTone" x1="0" y1="0" x2="1" y2="1">
        <stop offset="0" stop-color="#8a7c70"/>
        <stop offset="0.55" stop-color="#3b2e28"/>
        <stop offset="1" stop-color="#1f1a17"/>
      </linearGradient>
    </defs>
    <rect x="0" y="0" width="851" height="600" fill="url(#cafeTone)" role="img" aria-label="Foto: Gäste in einem Café vor einer Theke mit Kreidetafeln"/>
    <polygon points="0,355 0,500 330,545 140,420" fill="var(--red-glass)"/>
    <polygon points="851,205 851,640 420,555" fill="var(--charcoal)"/>
    <polygon points="0,500 420,555 851,640 851,760 0,760" fill="var(--paper)"/>
  </svg>

  <h1 class="headline">The advantages for the<br>customers oft he business</h1>

  <section class="benefits">
    <article class="benefit">
      <svg class="benefit-icon" viewBox="0 0 92 100">
        <polygon points="46,2 90,27 90,73 46,98 2,73 2,27" fill="var(--red)"/>
        <g fill="none" stroke="#fff" stroke-width="3" stroke-linecap="round" stroke-linejoin="round">
          <path d="M44 34 H62 V66 H44"/>
          <path d="M28 50 H52 M44 42 L52 50 L44 58"/>
        </g>
      </svg>
      <h2 class="benefit-title">Aufstehen<br>und Gehen</h2>
      <p class="benefit-text">Dank MesaOrder warten Ihre Kunden nie mehr auf eine Rechnung - MesaOrder Bestellungen werden immer gleich beim Bestellen bezahlt.</p>
    </article>

    <article class="benefit">
      <svg class="benefit-icon" viewBox="0 0 92 100">
        <polygon points="46,2 90,27 90,73 46,98 2,73 2,27" fill="var(--charcoal)"/>
        <g fill="none" stroke="#fff" stroke-width="3" stroke-linecap="round">
          <circle cx="46" cy="50" r="19"/>
          <path d="M46 38 V50 L54 56"/>
        </g>
      </svg>
      <h2 class="benefit-title is-dark">Wartezeiten<br>vermeiden</h2>
      <p class="benefit-text">Mit MesaOrder bestellen Ihre Kunden auf dem Smartphone jederzeit, vom jedem Tisch. Mit MesaOrder müssen Ihre Kunden nicht mehr Schlange stehen oder können ihr Essen bereits im Voraus bestellen und so Zeit sparen und haben ein verbessertes Nutzererlebnis.</p>
    </article>

    <article class="benefit">
      <svg class="benefit-icon" viewBox="0 0 92 100">
        <polygon points="46,2 90,27 90,73 46,98 2,73 2,27" fill="var(--red)"/>
        <g fill="none" stroke="#fff" stroke-width="3" stroke-linecap="round" stroke-linejoin="round">
          <rect x="35" y="30" width="22" height="40" rx="3"/>
          <path d="M43 64 H49"/>
        </g>
      </svg>
      <h2 class="benefit-title">MesaOrder<br>immer zur Hand</h2>
      <p class="benefit-text">Ihre Kunden erhalten die Menükarte auf dem Smartphone wenn Sie den QR-Code in Ihrem Unternehmen einscannen und bestellen einfach mit wenigen Tastenklicks.</p>
    </article>
  </section>

  <footer class="footer">
    <span class="page-number">4</span>
    <span class="footer-url">www.mesaorder.com</span>
  </footer>
</main>
</body>
</html>
```